Veluxa Bone & Motion Business Card

Need a business card using the logo provided. I want brand side of the card to be grey with the logo in the center of the card in white.

On the other side I leave to the designers

Target Market(s)

Personal Injury Attorneys

Industry/Entity Type

Medical

Contact Information for Business Card

Name, CEO. Cell Phone, (Hialeah, Address, Phone) (Homestead, Address, Phone) (Tallahassee, Address, Phone)

Colors

Designer to choose only greyscale colors for use in the design.

Requirements
Must have
• Logo by itself on one side

```html
<!DOCTYPE html>
<html lang="en">
<head>
<meta charset="utf-8">
<title>Veluxa Bone &amp; Motion Business Card</title>
<link rel="stylesheet" href="https://fonts.googleapis.com/css2?family=Montserrat:wght@400;500;600&display=swap">
<style>
  :root {
    --backdrop: #b0b1ad;
    --card-white: #ffffff;
    --card-brand: #8f9396;
    --ink-strong: #3a3d40;
    --ink-grey: #55595d;
    --ink-accent: #6e7276;
    --rule-grey: #8a8e92;
    --logo-white: #ffffff;
  }
  * { box-sizing: border-box; margin: 0; padding: 0; }
  html, body {
    width: 1200px;
    height: 801px;
    overflow: hidden;
    background: var(--backdrop);
    font-family: "Montserrat", sans-serif;
  }
  .sheet {
    width: 1200px;
    height: 801px;
    display: flex;
    align-items: center;
    justify-content: center;
    gap: 40px;
  }
  .card {
    width: 540px;
    height: 309px;
    border-radius: 16px;
    overflow: hidden;
    position: relative;
  }
  .card--contact {
    background: var(--card-white);
    display: flex;
    align-items: center;
  }
  .brand-block {
    width: 262px;
    padding-left: 32px;
    padding-right: 14px;
  }
  .brand-name {
    font-weight: 600;
    font-size: 20px;
    line-height: 1.2;
    letter-spacing: 0.06em;
    color: var(--ink-strong);
    text-transform: uppercase;
  }
  .divider {
    width: 1px;
    height: 180px;
    background: var(--rule-grey);
  }
  .contact-block {
    padding-left: 26px;
    font-size: 12.5px;
    line-height: 19px;
    color: var(--ink-grey);
  }
  .person-name {
    font-weight: 600;
    font-size: 19px;
    line-height: 22px;
    color: var(--ink-strong);
    letter-spacing: 0.02em;
  }
  .person-role { margin-bottom: 4px; }
  .contact-line { display: flex; align-items: center; gap: 6px; }
  .contact-line svg { width: 11px; height: 11px; flex: none; }
  .office-phone { color: var(--ink-accent); font-weight: 500; }
  .card--brand {
    background: var(--card-brand);
    display: flex;
    align-items: center;
    justify-content: center;
  }
  .brand-name--reversed {
    color: var(--logo-white);
    font-size: 34px;
    text-align: center;
  }
</style>
</head>
<body>
<main class="sheet">
  <section class="card card--contact">
    <div class="brand-block">
      <p class="brand-name">Veluxa<br>Bone &amp; Motion</p>
    </div>
    <div class="divider"></div>
    <div class="contact-block">
      <p class="person-name">DANIEL REYES</p>
      <p class="person-role">CEO</p>
      <p class="contact-line">
        <svg viewBox="0 0 12 12"><path d="M3 1l2 2.5-1.2 1.3c.7 1.5 1.8 2.6 3.4 3.4L8.5 7 11 9l-1.2 1.8C5.5 10.5 1.5 6.5 1.2 2.2z" fill="var(--ink-strong)"/></svg>
        888-555-0142
      </p>
      <p class="contact-line">
        <svg viewBox="0 0 12 12"><rect x="1" y="2.5" width="10" height="7" fill="none" stroke="var(--ink-strong)" stroke-width="1.2"/><path d="M1 2.5l5 4 5-4" fill="none" stroke="var(--ink-strong)" stroke-width="1.2"/></svg>
        hello@veluxabone.com
      </p>
      <p class="contact-line">
        <svg viewBox="0 0 12 12"><circle cx="6" cy="6" r="5" fill="none" stroke="var(--ink-strong)" stroke-width="1.2"/><path d="M1 6h10M6 1c-2.5 3-2.5 7 0 10M6 1c2.5 3 2.5 7 0 10" fill="none" stroke="var(--ink-strong)" stroke-width="1"/></svg>
        veluxabonemotion.com
      </p>
      <p>Hialeah, City in Florida</p>
      <p class="office-phone">P : +305 555-0180</p>
      <p>Homestead, City in Florida</p>
      <p class="office-phone">P : +305 555-0127</p>
      <p>Tallahassee, City in Florida</p>
      <p class="office-phone">P : +850 555-0163</p>
    </div>
  </section>
  <section class="card card--brand">
    <p class="brand-name brand-name--reversed">Veluxa<br>Bone &amp; Motion</p>
  </section>
</main>
</body>
</html>
```